Book Cover: Quiet Harbor: Small Ceremonies For The Restless Soul

I would like a full cover spread- front, back and spine as well as a stand alone front cover for Kindle for the book. Design a cover that mirrors the profound depth and dynamic energy of 'Quiet Harbor.' Envision a visual tapestry that draws readers into a transformative journey, where spirituality and self-care unite. Explore vibrant colors, intricate textures, and a sense of inner radiance that beckons readers to explore the book's rich wisdom within. See images for design inspiration attached. Even though some of the images are cartoon, I'd like the cover to be more serious than playful and very elegant.

About this book (back cover copy)
Are you ready to embark on a transformative journey and elevate your daily existence? "Quiet Harbor" is a treasure trove of practical yet profound rituals and wisdom from renowned self-care, healing, and spirituality experts.

Within these pages, you'll uncover a tapestry of guidance and insight from some of the world's most respected mentors. Their collective wisdom is your key to creating a sacred sanctuary within your everyday life.

From invigorating morning rituals to meditative practices, empowering affirmations, and transformative energy healing, you'll find a rich tapestry of tools to nurture a deeper connection with yourself and the universe.

Whether you're a seasoned practitioner or a newcomer to the world of self-care and spirituality, "Quiet Harbor" is your trusted companion on the journey to transform your life and elevate your daily experience. Open this book today and start your sacred, fulfilling adventure.

Colors
0094D4
00A9DD
6FCCEA
C7EBF8
E9F6FB
E54698
E96AAD
F1A4CE
F9D9EA
FCEFF6
6B429C
8869AF
B7A5CE
E3DAEB
F3F0F8

Requirements
Must have
• Title: Quiet Harbor: Subtitle: Small Ceremonies For The Restless Soul Name of Publisher: Lantern Bough Publishing- Logo on the back Back cover copy

```html
<!DOCTYPE html>
<html lang="en">
<head>
<meta charset="utf-8">
<title>Quiet Harbor – Front Cover</title>
<link rel="stylesheet" href="https://fonts.googleapis.com/css2?family=Dancing+Script:wght@500&family=Playfair+Display:ital,wght@0,400;1,600&display=swap">
<style>
  :root {
    --page: #ffffff;
    --plum-deep: #2f1648;
    --plum: #45185f;
    --plum-slate: #3a3350;
    --gold: #e9a55a;
    --gold-line: #d99a55;
    --gold-soft: rgba(233,165,90,0.55);
    --cream: #e6efe2;
    --white: #f7f4f8;
    --rose: #9a2f55;
    --crimson: #6e1f3f;
    --skin: #e8c9c4;
    --petal: #d9b2c9;
    --teal: #5fa9a0;
    --amber: #c98c4a;
  }
  * { margin: 0; padding: 0; box-sizing: border-box; }
  html, body {
    width: 1200px; height: 1200px; overflow: hidden;
    background: var(--page);
  }
  .cover {
    position: absolute; left: 233px; top: 50px;
    width: 734px; height: 1100px;
    background: linear-gradient(100deg, var(--plum-slate) 0%, var(--plum) 50%, var(--plum-deep) 100%);
    overflow: hidden;
  }
  .cover-photo {
    position: absolute; left: 50px; top: 40px;
    width: 634px; height: 640px;
    border-radius: 46% 46% 40% 40% / 38% 38% 50% 50%;
    background:
      radial-gradient(ellipse 18% 12% at 50% 14%, var(--skin) 0%, rgba(232,201,196,0) 100%),
      radial-gradient(ellipse 22% 18% at 30% 40%, var(--petal) 0%, rgba(217,178,201,0) 100%),
      radial-gradient(ellipse 18% 20% at 72% 52%, var(--teal) 0%, rgba(95,169,160,0) 100%),
      radial-gradient(ellipse 20% 16% at 40% 62%, var(--amber) 0%, rgba(201,140,74,0) 100%),
      radial-gradient(ellipse 22% 10% at 50% 90%, var(--skin) 0%, rgba(232,201,196,0) 100%),
      radial-gradient(ellipse 50% 50% at 50% 50%, var(--rose) 0%, var(--crimson) 55%, rgba(69,24,95,0) 100%);
  }
  .frame { position: absolute; inset: 0; pointer-events: none; }
  .ornament { position: absolute; }
  .ornament--corner-tl { left: 18px; top: 25px; width: 150px; height: 218px;
    background: radial-gradient(ellipse 100% 100% at 0% 0%, var(--gold-soft), rgba(233,165,90,0) 75%); }
  .ornament--corner-tr { right: 18px; top: 25px; width: 150px; height: 218px;
    background: radial-gradient(ellipse 100% 100% at 100% 0%, var(--gold-soft), rgba(233,165,90,0) 75%); }
  .ornament--corner-bl { left: 18px; bottom: 25px; width: 150px; height: 218px;
    background: radial-gradient(ellipse 100% 100% at 0% 100%, var(--gold-soft), rgba(233,165,90,0) 75%); }
  .ornament--corner-br { right: 18px; bottom: 25px; width: 150px; height: 218px;
    background: radial-gradient(ellipse 100% 100% at 100% 100%, var(--gold-soft), rgba(233,165,90,0) 75%); }
  .ornament--top, .ornament--bottom { left: 272px; width: 190px; height: 30px;
    background: radial-gradient(ellipse at center, var(--gold-soft), rgba(233,165,90,0) 72%); }
  .ornament--top { top: 18px; }
  .ornament--bottom { bottom: 18px; }
  .ornament--side-l, .ornament--side-r { top: 456px; width: 36px; height: 192px;
    background: radial-gradient(ellipse at center, var(--gold-soft), rgba(233,165,90,0) 72%); }
  .ornament--side-l { left: 14px; }
  .ornament--side-r { right: 14px; }

  .title {
    position: absolute; left: 0; right: 0; top: 672px;
    text-align: center;
    font-family: "Dancing Script", cursive;
    font-weight: 500;
    font-size: 122px; line-height: 1;
    color: var(--gold);
    white-space: nowrap;
  }
  .subtitle {
    position: absolute; left: 0; right: 0; top: 813px;
    text-align: center;
    font-family: "Playfair Display", serif;
    font-style: italic; font-weight: 600;
    font-size: 31px; line-height: 38px;
    color: var(--cream);
  }
  .author {
    position: absolute; left: 0; right: 0; top: 958px;
    text-align: center;
    font-family: "Playfair Display", serif;
    font-size: 26px; letter-spacing: 17px;
    padding-left: 17px;
    color: var(--white);
  }
</style>
</head>
<body>
  <main class="cover">
    <div class="cover-photo" role="img" aria-label="Photograph of a woman in a crimson dress holding an armful of dried flowers, apothecary bottles, old books and trinkets against her chest"></div>

    <div class="ornament ornament--corner-tl" role="img" aria-label="Gold filigree corner flourish"></div>
    <div class="ornament ornament--corner-tr" role="img" aria-label="Gold filigree corner flourish"></div>
    <div class="ornament ornament--corner-bl" role="img" aria-label="Gold filigree corner flourish"></div>
    <div class="ornament ornament--corner-br" role="img" aria-label="Gold filigree corner flourish"></div>
    <div class="ornament ornament--top" role="img" aria-label="Gold filigree header flourish"></div>
    <div class="ornament ornament--bottom" role="img" aria-label="Gold filigree footer flourish"></div>
    <div class="ornament ornament--side-l" role="img" aria-label="Gold filigree side flourish"></div>
    <div class="ornament ornament--side-r" role="img" aria-label="Gold filigree side flourish"></div>

    <svg class="frame" width="734" height="1100" viewBox="0 0 734 1100" aria-hidden="true">
      <g stroke="var(--gold-line)" stroke-width="1.4" fill="none">
        <line x1="184" y1="38" x2="258" y2="38"/><line x1="184" y1="42" x2="258" y2="42"/>
        <line x1="476" y1="38" x2="550" y2="38"/><line x1="476" y1="42" x2="550" y2="42"/>
        <line x1="184" y1="1058" x2="258" y2="1058"/><line x1="184" y1="1062" x2="258" y2="1062"/>
        <line x1="476" y1="1058" x2="550" y2="1058"/><line x1="476" y1="1062" x2="550" y2="1062"/>
        <line x1="30" y1="264" x2="30" y2="444"/><line x1="35" y1="264" x2="35" y2="444"/>
        <line x1="30" y1="658" x2="30" y2="835"/><line x1="35" y1="658" x2="35" y2="835"/>
        <line x1="699" y1="264" x2="699" y2="444"/><line x1="704" y1="264" x2="704" y2="444"/>
        <line x1="699" y1="658" x2="699" y2="835"/><line x1="704" y1="658" x2="704" y2="835"/>
      </g>
    </svg>

    <h1 class="title">Quiet Harbor</h1>
    <p class="subtitle">Small Ceremonies For The<br>Restless Soul</p>
    <p class="author">AUTHOR NAME</p>
  </main>
</body>
</html>
```